Lentil and Vegetable Soup (Sambar) Product Label Design

Sambar is the product and we need a label for that. The label size is 4"x3.33". Attached is the sample label containing all the necessary info.
Mainly show the images of the coconut, onions, chayotes, big egg plant and the lentils (Toor dal). Various design choices are encouraged. This includes various types of fonts, colors, backgrounds, etc.

```html
<!DOCTYPE html>
<html lang="en">
<head>
<meta charset="UTF-8">
<title>Vellora Samber Label</title>
<link rel="stylesheet" href="https://fonts.googleapis.com/css2?family=Lobster&family=Oswald:wght@500;700&family=Roboto:wght@400;700&display=swap">
<style>
  :root {
    --page-bg: #e6e6e6;
    --label-white: #ffffff;
    --leaf-green: #8dc63f;
    --leaf-green-deep: #6aa82b;
    --ink-green: #2f6b1e;
    --chilli-red: #d3202a;
    --turmeric: #f2a51c;
    --soup-cream: #fff6c9;
    --text-dark: #2b2b2b;
  }
  * { box-sizing: border-box; margin: 0; padding: 0; }
  html, body { width: 831px; height: 1200px; overflow: hidden; }
  body {
    background: var(--page-bg);
    font-family: "Roboto", Arial, sans-serif;
    position: relative;
  }
  .label {
    position: absolute;
    left: 66px; top: 170px;
    width: 700px; height: 860px;
    background: var(--label-white);
    overflow: hidden;
    box-shadow: 0 2px 10px rgba(0,0,0,.15);
  }
  .label__header {
    height: 190px;
    display: flex; align-items: center; justify-content: center;
    border-bottom: 6px solid var(--leaf-green);
  }
  .brand {
    font-family: "Lobster", cursive;
    font-size: 96px;
    color: var(--chilli-red);
    letter-spacing: 1px;
  }
  .label__body {
    position: absolute;
    left: 0; top: 196px;
    width: 100%; height: 560px;
    background: linear-gradient(180deg, var(--leaf-green) 0%, var(--leaf-green-deep) 100%);
  }
  .ingredients, .directions {
    position: absolute;
    top: 30px;
    width: 130px;
    font-size: 13px;
    line-height: 1.55;
    color: var(--text-dark);
  }
  .ingredients { left: 24px; }
  .directions { right: 24px; text-align: right; font-weight: 700; }
  .badge {
    position: absolute;
    left: 180px; top: 20px;
    width: 340px; height: 340px;
    border-radius: 50%;
    background: var(--label-white);
    padding: 10px;
  }
  .badge__inner {
    width: 100%; height: 100%;
    border-radius: 50%;
    background: var(--leaf-green);
    border: 4px solid var(--turmeric);
    overflow: hidden;
    position: relative;
    text-align: center;
  }
  .badge__soup {
    position: absolute; left: 0; top: 0; width: 100%; height: 95px;
    background: linear-gradient(180deg, var(--turmeric), #f7cf5a);
  }
  .product-name {
    position: absolute; left: 0; right: 0; top: 98px;
    font-family: "Oswald", sans-serif;
    font-weight: 700;
    font-size: 36px;
    color: var(--chilli-red);
    letter-spacing: 1px;
  }
  .product-variant {
    position: absolute; left: 0; right: 0; top: 146px;
    font-family: "Oswald", sans-serif;
    font-weight: 500;
    font-size: 23px;
    color: var(--ink-green);
  }
  .badge__produce {
    position: absolute; left: 0; top: 190px; width: 100%; height: 140px;
    background: radial-gradient(ellipse at 35% 50%, #efe6d2 0%, #b98a5a 35%, transparent 60%),
                radial-gradient(ellipse at 70% 55%, #a8324f 0%, #5c2a5e 40%, transparent 65%),
                var(--leaf-green);
  }
  .tagline {
    position: absolute;
    left: 0; right: 0; top: 392px;
    text-align: center;
    font-family: "Lobster", cursive;
    font-size: 46px;
    color: var(--soup-cream);
  }
  .label__rule {
    position: absolute; left: 0; right: 0; top: 480px;
    height: 4px; background: var(--turmeric);
  }
  .net-weight {
    position: absolute; left: 0; right: 0; top: 498px;
    text-align: center;
    font-family: "Oswald", sans-serif;
    font-weight: 700;
    font-size: 28px;
    color: var(--label-white);
  }
  .label__footer {
    position: absolute; left: 0; bottom: 0; width: 100%; height: 104px;
    background: var(--label-white);
    border-top: 6px solid var(--chilli-red);
  }
</style>
</head>
<body>
  <main class="label">
    <header class="label__header">
      <span class="brand">Vellora</span>
    </header>

    <section class="label__body">
      <p class="ingredients">Ingredients: Toor Dal (Split Pigeon Peas), Coconut, Onion, Chayote, Brinjal, Tamarind, Tomato, Red Chilli, Coriander, Turmeric, Mustard Seeds, Curry Leaves, Salt, Asafoetida, Edible Oil.</p>

      <div class="badge">
        <div class="badge__inner">
          <div class="badge__soup" role="img" aria-label="Bowl of sambar with lentils"></div>
          <h1 class="product-name">SAMBER</h1>
          <p class="product-variant">Coconut &amp; Onion Special</p>
          <div class="badge__produce" role="img" aria-label="Coconut halves, red onions, chayote and eggplant"></div>
        </div>
      </div>

      <p class="directions">Microwave for 2 minutes. Stir well and serve hot with rice or idli. Keep refrigerated after opening.</p>

      <p class="tagline">Spicy Lentil Soup</p>
      <div class="label__rule"></div>
      <p class="net-weight">Net Wt.: 900 Gsm (1.98 lbs)</p>
    </section>

    <footer class="label__footer"></footer>
  </main>
</body>
</html>
```